Direct to Consumer extended service contract business with a new disruptive business model needs a

We need a customized wordpress design for a company called 'Bright Harbor Assurance'.
We provide an innovative and unique service contract protection program direct to consumers. This program provides monthly coverage for all electronics purchased in the last 4 years and all electronics the consumer purchases in the future for a low monthly fee. The overall design should communicate a sense of legitimacy, ethics, and superior customer service and support (in an industry that has a huge PR issue to overcome).
Electronics is the first product group, other product groups with different price points to launch in the future..

Target Market(s)

All purchasers of electronic goods...all demographics

Industry/Entity Type

Electronics

Font styles to use
Sans Serif

Requirements
Must have
• Customer Testimonials
Industry News
Customer ratings
Blog posts
Call to action messaging
Like the functional elements and design of quillmesa.example (need to be better)
Nice to have
• Like to see video testimonials
Social network "whats trending related to electronics or service contract industry"
Easy way to register products for warranty

```html
<!DOCTYPE html>
<html lang="en">
<head>
<meta charset="utf-8">
<title>Bright Harbor Assurance</title>
<link rel="stylesheet" href="https://fonts.googleapis.com/css2?family=Open+Sans:wght@400;600;700&family=Oswald:wght@400;500&display=swap">
<style>
:root{
  --topbar:#23262b;
  --dark:#2b2b2b;
  --footer:#2a2a2a;
  --bottombar:#1e1f21;
  --green:#27ae5f;
  --green-dark:#167a3f;
  --orange:#f0a31c;
  --text:#555;
  --muted:#999;
  --light:#e6e6e6;
  --white:#fff;
}
*{margin:0;padding:0;box-sizing:border-box}
html,body{width:1200px;height:2228px;overflow:hidden}
body{font-family:"Open Sans",Arial,sans-serif;color:var(--text);background:var(--white);position:relative}
.wrap{width:856px;margin:0 auto;position:relative;height:100%}
a{color:inherit;text-decoration:none}

.topbar{height:37px;background:var(--topbar);color:#ddd;font-size:13px}
.topbar .phone{position:absolute;left:0;top:10px}
.topbar .links{position:absolute;left:527px;top:10px}
.topbar .links span{margin:0 8px;color:#888}
.topbar .follow{position:absolute;left:670px;top:10px}
.topbar .icons{position:absolute;left:752px;top:10px;display:flex;gap:22px}
.topbar .icons i{display:block;width:12px;height:12px;border-radius:50%;background:#aaa}

.header{height:107px;background:var(--white)}
.brand{position:absolute;left:2px;top:34px;display:flex;align-items:center;gap:10px;font-weight:700;font-size:24px;color:var(--green)}
.brand .mark{width:22px;height:22px;background:var(--green)}
.nav{position:absolute;right:0;top:45px;display:flex;gap:33px;font-size:16px;color:#666}

.hero{height:463px;background:linear-gradient(100deg,#d9d6d2 0%,#eef0f1 35%,#e7e9ec 60%,#c9b9b0 85%,#b7464f 100%);position:relative}
.hero .arrow{position:absolute;top:240px;width:34px;height:34px;border-radius:50%;background:#3a3a3a}
.hero .arrow svg{position:absolute;left:10px;top:9px}
.hero .prev{left:53px}.hero .next{left:1116px}

.cta{height:91px;background:var(--dark)}
.cta h2{position:absolute;left:0;top:18px;font-family:"Oswald",Arial,sans-serif;font-weight:500;font-size:42px;color:var(--white);letter-spacing:-.5px}
.btn-signup{position:absolute;left:719px;top:24px;width:138px;height:45px;background:var(--green);color:var(--white);font-size:18px;font-weight:600;display:flex;align-items:center;justify-content:center;border-radius:2px}

.testimonials{height:356px}
.video{position:absolute;left:0;top:47px;width:392px;height:260px;background:linear-gradient(135deg,#cfd8e2,#9eb3c9 55%,#5c6f80)}
.video .play{position:absolute;left:150px;top:75px}
.video .bar{position:absolute;left:0;bottom:0;width:100%;height:32px;background:#222}
.video .track{position:absolute;left:20px;top:12px;width:290px;height:6px;background:#555}
.video .track i{display:block;width:125px;height:100%;background:#3aa0e0}
.video .tools{position:absolute;right:10px;top:18px;display:flex;flex-direction:column;gap:6px}
.video .tools i{display:block;width:30px;height:24px;background:#333;border-radius:2px}
.testi-text{position:absolute;left:419px;top:0;width:437px}
.testi-text h2{margin-top:40px;font-family:"Oswald",Arial,sans-serif;font-weight:400;font-size:34px;color:#333;line-height:42px}
.testi-text .sub{margin-top:12px;color:var(--green);font-size:16px}
.testi-text p.body{margin-top:16px;font-size:12px;line-height:20.5px;color:var(--muted)}
.btn-watch{display:inline-flex;align-items:center;justify-content:center;margin-top:20px;width:157px;height:39px;background:var(--orange);color:var(--white);font-size:16px;border-radius:2px}

.news{height:434px;background:linear-gradient(90deg,#1c1c1e,#2a2b2e 50%,#1b1b1c);color:var(--white)}
.section-title{position:absolute;left:0;width:100%;text-align:center;font-size:26px}
.news .section-title{top:22px}
.cards{position:absolute;left:0;width:100%;display:flex;justify-content:space-between}
.news .cards{top:85px}
.card{width:263px}
.card .photo{height:148px}
.news .card h3{margin-top:25px;font-weight:400;font-size:15.5px;line-height:23px;color:#888}
.news .card p{margin-top:16px;font-size:11px;line-height:20.5px;color:#888;text-align:justify}

.blog{height:442px}
.blog .section-title{top:22px;color:#555}
.blog .cards{top:79px}
.blog .card .photo{height:160px}
.post-head{margin-top:13px;display:flex;background:#f5f5f5;height:55px}
.date{width:37px;display:flex;flex-direction:column;font-size:11px;color:var(--white);text-align:center}
.date .d{background:var(--green-dark);height:28px;line-height:28px}
.date .m{background:#555;flex:1;line-height:27px}
.post-head h3{font-weight:400;font-size:14px;line-height:21px;color:#777;padding:6px 0 0 10px}
.blog .card p{margin-top:18px;font-size:11px;line-height:19px;color:var(--muted);text-align:justify}

.footer{height:238px;background:var(--footer);color:#ccc}
.footer h4{font-weight:400;font-size:17px;color:#ddd;position:absolute;top:18px}
.feed{position:absolute;left:0;top:58px;width:225px}
.feed .item{display:flex;gap:14px;padding-bottom:14px;border-bottom:1px solid #3d3d3d;margin-bottom:14px}
.feed .item:last-child{border:0}
.feed .avatar{width:56px;height:52px;background:linear-gradient(#8fa4b8,#cdd6de);flex:none}
.feed p{font-style:italic;font-size:10.5px;line-height:20px;color:#aaa}
.ratings{position:absolute;left:319px;top:58px}
.stars{display:flex;gap:2px}
.ratings .store{margin-top:8px;font-size:15px;color:#ddd}
.ratings .avg{margin-top:8px;font-size:13px;color:#ccc}
.ratings .read{margin-top:8px;font-size:10px;color:#aaa}
.socials{margin-top:16px;display:flex;gap:24px}
.socials div{text-align:center;font-size:8px;color:#999;width:48px}
.socials i{display:block;width:36px;height:36px;border:1.5px solid #999;border-radius:50%;margin:0 auto 4px}
.office{position:absolute;left:608px;top:63px;width:248px;height:154px;border:1px solid #4a4a4a;padding:12px 18px}
.office h5{font-weight:400;font-size:15px;color:#aaa}
.office .addr{margin-top:10px;font-size:11.5px;line-height:21px;color:#888}
.office .line{margin-top:14px;display:flex;align-items:center;gap:10px;font-size:12px;color:#999}
.office .line + .line{margin-top:8px}

.bottombar{height:60px;background:var(--bottombar);font-size:11px;color:#888}
.bottombar .copy{position:absolute;left:21px;top:22px}
.bottombar .menu{position:absolute;right:0;top:22px}
.bottombar .menu span{margin:0 10px;color:#555}
</style>
</head>
<body>

<div class="topbar"><div class="wrap">
  <span class="phone">855-500-HARBOR (4272)</span>
  <span class="links"><a href="#">Login</a><span>|</span><a href="#">Support</a></span>
  <span class="follow">Follow Us :</span>
  <span class="icons"><i></i><i></i><i></i></span>
</div></div>

<header class="header"><div class="wrap">
  <div class="brand"><span class="mark"></span>Bright Harbor Assurance</div>
  <nav class="nav"><a href="#">Home</a><a href="#">Plans</a><a href="#">Benefits</a><a href="#">FAQs</a><a href="#">About Us</a></nav>
</div></header>

<section class="hero" role="img" aria-label="Photo of a man in a white shirt at a desk with a laptop and clipboard, bookshelves behind">
  <span class="arrow prev"><svg width="14" height="16" viewBox="0 0 14 16"><path d="M10 2 4 8l6 6" stroke="#fff" stroke-width="2.5" fill="none"/></svg></span>
  <span class="arrow next"><svg width="14" height="16" viewBox="0 0 14 16"><path d="M4 2l6 6-6 6" stroke="#fff" stroke-width="2.5" fill="none"/></svg></span>
</section>

<section class="cta"><div class="wrap">
  <h2>Get Your Bright Harbor Assurance Today!</h2>
  <a class="btn-signup" href="#">Sign Up &gt;</a>
</div></section>

<section class="testimonials"><div class="wrap">
  <div class="video" role="img" aria-label="Video still of a customer testimonial with construction workers in hard hats">
    <svg class="play" width="90" height="90" viewBox="0 0 90 90"><circle cx="45" cy="45" r="40" fill="none" stroke="#fff" stroke-width="6"/><path d="M36 27v36l28-18z" fill="#fff"/></svg>
    <div class="tools"><i></i><i></i><i></i></div>
    <div class="bar"><div class="track"><i></i></div></div>
  </div>
  <div class="testi-text">
    <h2>Customer Testimonials</h2>
    <p class="sub">Please watch the video to know more about our site.</p>
    <p class="body">Lorem ipsum dolor sit amet, consectetur adipiscing elit, sed do eiusmod tempor incididunt ut labore et dolore magna aliqua. Ut enim ad minim veniam, quis nostrud exercitation ullamco laboris nisi ut aliquip ex ea commodo consequat. Duis aute irure dolor in reprehenderit in voluptate velit esse cillum dolore eu fugiat nulla pariatur. Excepteur sint occaecat cupidatat non proident, sunt in culpa qui officia deserunt mollit anim id est laborum.</p>
    <a class="btn-watch" href="#">Watch the video</a>
  </div>
</div></section>

<section class="news"><div class="wrap">
  <h2 class="section-title" style="font-weight:400">Industry News</h2>
  <div class="cards">
    <article class="card">
      <div class="photo" role="img" aria-label="Industrial power plant by the sea" style="background:linear-gradient(#3b6fb0,#9fb6c9 55%,#4d6b86)"></div>
      <h3>Sed ut perspiciatis unde omnis iste natus error sit &nbsp;unde omnis</h3>
      <p>Lorem ipsum dolor sit amet, consectetur adipisicing elit, sed do eiusmod tempor inci didunt ut labore. Lorem ipsum dolor sit amet, consectetur adipisicing elit consectetur adipisicing elit</p>
    </article>
    <article class="card">
      <div class="photo" role="img" aria-label="Engineer in a hard hat at industrial machinery" style="background:linear-gradient(135deg,#9cc3dc,#2f4f80 55%,#6c8aa8)"></div>
      <h3>Sed ut perspiciatis unde omnis iste natus error sit &nbsp;unde omnis</h3>
      <p>Lorem ipsum dolor sit amet, consectetur adipisicing elit, sed do eiusmod tempor inci didunt ut labore. Lorem ipsum dolor sit amet, consectetur adipisicing elit consectetur adipisicing elit</p>
    </article>
    <article class="card">
      <div class="photo" role="img" aria-label="City skyline at dusk with a tall tower" style="background:linear-gradient(#3a2f8f,#6b4fb0 50%,#c07a6a)"></div>
      <h3>Sed ut perspiciatis unde omnis iste natus error sit &nbsp;unde omnis</h3>
      <p>Lorem ipsum dolor sit amet, consectetur adipisicing elit, sed do eiusmod tempor inci didunt ut labore. Lorem ipsum dolor sit amet, consectetur adipisicing elit consectetur adipisicing elit</p>
    </article>
  </div>
</div></section>

<section class="blog"><div class="wrap">
  <h2 class="section-title" style="font-weight:400">Blog Posts</h2>
  <div class="cards">
    <article class="card">
      <div class="photo" role="img" aria-label="Woman smiling beside a laptop" style="background:linear-gradient(135deg,#b9d6e8,#6e9cc0 60%,#c9a78a)"></div>
      <div class="post-head"><div class="date"><span class="d">15</span><span class="m">Aug</span></div><h3>Sed ut perspiciatis unde omnis iste natus error sit</h3></div>
      <p>Lorem ipsum dolor sit amet, consectetur adipiscing elit, sed do eiusmod tempor incididunt ut labore et dolore magna aliqua. Ut enim ad minim veniam, quis nostrud exercitation ullamco laboris nisi ut aliquip ex ea commodo</p>
    </article>
    <article class="card">
      <div class="photo" role="img" aria-label="Hands typing on a laptop keyboard" style="background:linear-gradient(135deg,#f2f2f2,#bbbbbb 55%,#1c1c1c)"></div>
      <div class="post-head"><div class="date"><span class="d">15</span><span class="m">Aug</span></div><h3>Sed ut perspiciatis unde omnis iste natus error sit</h3></div>
      <p>Lorem ipsum dolor sit amet, consectetur adipiscing elit, sed do eiusmod tempor incididunt ut labore et dolore magna aliqua. Ut enim ad minim veniam, quis nostrud exercitation ullamco laboris nisi ut aliquip ex ea commodo</p>
    </article>
    <article class="card">
      <div class="photo" role="img" aria-label="Smartphone resting on a keyboard" style="background:linear-gradient(135deg,#3a3a3a,#d8d8d8 50%,#2a2a2a)"></div>
      <div class="post-head"><div class="date"><span class="d">15</span><span class="m">Aug</span></div><h3>Sed ut perspiciatis unde omnis iste natus error sit</h3></div>
      <p>Lorem ipsum dolor sit amet, consectetur adipiscing elit, sed do eiusmod tempor incididunt ut labore et dolore magna aliqua. Ut enim ad minim veniam, quis nostrud exercitation ullamco laboris nisi ut aliquip ex ea commodo</p>
    </article>
  </div>
</div></section>

<footer class="footer"><div class="wrap">
  <h4 style="left:0">Community Feed</h4>
  <div class="feed">
    <div class="item"><div class="avatar" role="img" aria-label="Member portrait"></div><p>Atcurs usuctu aecenas tristique Uls pharetra mec accumsan. Atcurs usuctu aecenas tristique</p></div>
    <div class="item"><div class="avatar" role="img" aria-label="Member portrait"></div><p>Atcurs usuctu aecenas tristique Uls pharetra mec accumsan. Atcurs usuctu aecenas tristique</p></div>
  </div>

  <h4 style="left:319px">Customer Ratings</h4>
  <div class="ratings">
    <div class="stars">
      <svg width="84" height="16" viewBox="0 0 84 16">
        <g fill="#f0a31c"><path id="s" d="M8 1l2.1 4.6 5 .5-3.8 3.4 1.1 5L8 12 3.6 14.5l1.1-5L.9 6.1l5-.5z"/><use href="#s" x="17"/><use href="#s" x="34"/></g>
        <g fill="#ddd"><use href="#s" x="51"/><use href="#s" x="68"/></g>
      </svg>
    </div>
    <div class="store">Device App Market</div>
    <div class="avg">4.5 average on 7000+ reviews</div>
    <div class="read">Read the reviews</div>
    <div class="socials"><div><i></i>social</div><div><i></i>updates</div><div><i></i>circles</div></div>
  </div>

  <h4 style="left:604px">Get In Touch</h4>
  <div class="office">
    <h5>Corporate Office</h5>
    <div class="addr">1450 Lantern Cove Road<br>Suite 210 Port Weller, USA</div>
    <div class="line"><svg width="16" height="16" viewBox="0 0 16 16"><path d="M3 1l3 3-1.5 2a9 9 0 0 0 5.5 5.5L12 10l3 3-2 2C7 15 1 9 1 3z" fill="none" stroke="#999" stroke-width="1.3"/></svg>Phone: (855) 500-4272</div>
    <div class="line"><svg width="16" height="12" viewBox="0 0 16 12"><rect x=".7" y=".7" width="14.6" height="10.6" fill="none" stroke="#999" stroke-width="1.3"/><path d="M1 1l7 6 7-6" fill="none" stroke="#999" stroke-width="1.3"/></svg>support@brightharbor.example</div>
  </div>
</div></footer>

<div class="bottombar"><div class="wrap">
  <span class="copy">©2013 - 2014 &nbsp;Bright Harbor Assurance, All Rights Reserved.</span>
  <span class="menu"><a href="#">Home</a><span>|</span><a href="#">Plans</a><span>|</span><a href="#">About Us</a><span>|</span><a href="#">Contacts</a></span>
</div></div>

</body>
</html>
```